Harborline Renewal Business Card Design

Professional and clean design. The design colors should flow with the logo. Two-sided card with the website on the back which is:

www.HarborlineRenewal.example.

"Specializing in Water Damage Restoration"

On the front I need the name, email, phone, and logo.

Name: Darnell Quisby
Email: Darnell@HarborlineRenewal.example
Phone: 555-318-2046 for now

I only have the Preview and Thumbnail right now but should have the source files uploaded within a day or two.

Target Market(s)

Flood victims, home owners with water damage from busted pipes etc...

Industry/Entity Type

Business

Contact Information for Business Card

Name: Darnell Quisby

Font styles to use
Serif
Sans Serif

Requirements
Must have
• Business Card Details Info

```html
<!DOCTYPE html>
<html lang="en">
<head>
<meta charset="utf-8">
<title>Harborline Renewal Business Card</title>
<link rel="stylesheet" href="https://fonts.googleapis.com/css2?family=Cinzel:wght@600&family=Open+Sans:wght@400;700&display=swap">
<style>
  :root {
    --backdrop: #2b2b2c;
    --card: #000000;
    --blue: #2a9ad8;
    --blue-light: #4fc0f0;
    --radius: 22px;
  }
  * { margin: 0; padding: 0; box-sizing: border-box; }
  html, body { width: 1200px; height: 900px; overflow: hidden; }
  body { background: var(--backdrop); position: relative; font-family: "Open Sans", sans-serif; }

  .card {
    position: absolute;
    width: 600px;
    height: 343px;
    background: var(--card);
    border-radius: var(--radius);
    overflow: hidden;
    box-shadow: 0 18px 40px rgba(0,0,0,.55);
  }

  /* Back side */
  .card-back { left: 80px; top: 100px; }
  .back-brand {
    position: absolute; left: 0; right: 0; top: 52px;
    display: flex; flex-direction: column; align-items: center;
  }
  .brand-dot {
    width: 120px; height: 120px; border-radius: 50%;
    background: var(--blue-light);
  }
  .back-brand .brand-name {
    margin-top: 16px;
    font-family: "Cinzel", serif; font-weight: 600;
    font-size: 26px; letter-spacing: 2px; color: var(--blue);
  }
  .tagline {
    position: absolute; left: 0; right: 0; top: 252px; text-align: center;
    font-size: 16px; letter-spacing: .5px; color: var(--blue);
    text-transform: uppercase;
  }
  .back-web {
    position: absolute; left: 0; right: 0; top: 280px; text-align: center;
    font-size: 16px; color: var(--blue);
  }

  /* Front side */
  .card-front { left: 520px; top: 490px; }
  .front-brand {
    position: absolute; left: 40px; top: 40px;
    display: flex; align-items: center; gap: 14px;
  }
  .front-brand .brand-dot { width: 56px; height: 56px; background: var(--blue); }
  .front-brand .brand-name {
    font-family: "Cinzel", serif; font-weight: 600;
    font-size: 24px; letter-spacing: 2px; color: var(--blue);
  }
  .person-name {
    position: absolute; right: 40px; top: 164px;
    font-weight: 700; font-size: 24px; letter-spacing: .5px;
    color: var(--blue); text-transform: uppercase;
  }
  .divider {
    position: absolute; left: 30px; right: 30px; top: 204px;
    height: 2px; background: var(--blue);
  }
  .contact-list {
    position: absolute; left: 36px; top: 216px; list-style: none;
  }
  .contact-list li {
    display: flex; align-items: center; gap: 10px;
    font-size: 16px; line-height: 23px; color: var(--blue);
  }
  .contact-list svg { width: 14px; height: 14px; fill: var(--blue); flex: none; }
  .footer-band {
    position: absolute; left: 0; right: 0; bottom: 0; height: 30px;
    background: var(--blue);
  }
</style>
</head>
<body>

  <section class="card card-back">
    <div class="back-brand">
      <div class="brand-dot"></div>
      <div class="brand-name">Harborline Renewal</div>
    </div>
    <p class="tagline">Specializing in Water Damage Restoration</p>
    <p class="back-web">www.HarborlineRenewal.example</p>
  </section>

  <section class="card card-front">
    <div class="front-brand">
      <div class="brand-dot"></div>
      <div class="brand-name">Harborline Renewal</div>
    </div>
    <h1 class="person-name">Darnell Quisby</h1>
    <div class="divider"></div>
    <ul class="contact-list">
      <li>
        <svg viewBox="0 0 24 24" aria-hidden="true"><path d="M6.6 10.8a15.1 15.1 0 0 0 6.6 6.6l2.2-2.2a1 1 0 0 1 1-.25 11.4 11.4 0 0 0 3.6.57 1 1 0 0 1 1 1V20a1 1 0 0 1-1 1A17 17 0 0 1 3 4a1 1 0 0 1 1-1h3.5a1 1 0 0 1 1 1c0 1.25.2 2.45.57 3.57a1 1 0 0 1-.25 1z"/></svg>
        555-318-2046
      </li>
      <li>
        <svg viewBox="0 0 24 24" aria-hidden="true"><path d="M2 5h20v14H2z M4 7v.5l8 5 8-5V7z" fill-rule="evenodd"/></svg>
        Darnell@HarborlineRenewal.example
      </li>
      <li>
        <svg viewBox="0 0 24 24" aria-hidden="true"><path d="M12 2a10 10 0 1 0 0 20 10 10 0 0 0 0-20zm6.9 6h-2.9a15 15 0 0 0-1.4-3.6A8 8 0 0 1 18.9 8zM12 4c.8 1.2 1.5 2.5 1.9 4h-3.8c.4-1.5 1.1-2.8 1.9-4zM4.3 14a8 8 0 0 1 0-4h3.4a16 16 0 0 0 0 4zm.8 2h2.9c.3 1.3.8 2.5 1.4 3.6A8 8 0 0 1 5.1 16zM8 8H5.1a8 8 0 0 1 4.3-3.6C8.8 5.5 8.3 6.7 8 8zm4 12c-.8-1.2-1.5-2.5-1.9-4h3.8c-.4 1.5-1.1 2.8-1.9 4zm2.3-6H9.7a14 14 0 0 1 0-4h4.6a14 14 0 0 1 0 4zm.3 5.6c.6-1.1 1.1-2.3 1.4-3.6h2.9a8 8 0 0 1-4.3 3.6zm1.7-5.6a16 16 0 0 0 0-4h3.4a8 8 0 0 1 0 4z"/></svg>
        www.HarborlineRenewal.example
      </li>
    </ul>
    <div class="footer-band"></div>
  </section>

</body>
</html>
```